Management Consultancy needs sharp professional services showcased in a brochure

We are a management consultancy specializing on contract management and conflict avoidance services requiring a professional brochure showcasing our services to prospective clients.

Attached are a selection of existing stationary and the colour scheme.

Further details on our company can be found at www.velt-advisory-partners.com
Updates

Preference is for bi-fold, however, innovative tri-fold will be considered. Added Monday, August 7, 2017

Target Market(s)

Construction companies, consultants, developers, oil and gas service providers, NGO's, SME's.

Industry/Entity Type

Management

Requirements
Must have
• High degree of professionalism with eye catching, sharp detail. No frils.
• Colour scheme as per the attachments
• Font as per attachments - Century Gothic
• Details of our company and services
Nice to have
• Open to ideas, thinking along the lines of a car brochure type design.
• Bi-fold preferred, by trifold accepted if innovative.
Should not have
• Remove reference to the United Arab Emirates.
• No cartoon/clipart photos.

```html
<!DOCTYPE html>
<html lang="en">
<head>
<meta charset="utf-8">
<title>Velt Advisory – Brochure Cover Spread</title>
<link rel="stylesheet" href="https://fonts.googleapis.com/css2?family=Didact+Gothic&family=Montserrat:wght@600&family=Libre+Baskerville:ital,wght@1,700&display=swap">
<style>
  :root {
    --navy: #1c2a4f;
    --red: #a01f2f;
    --paper: #ffffff;
    --paper-shade: #eef0f4;
    --ink-soft: #6a7080;
    --canvas: #d9dbe0;
  }
  * { box-sizing: border-box; margin: 0; padding: 0; }
  html, body { width: 914px; height: 1200px; overflow: hidden; background: var(--canvas); }
  body { font-family: "Didact Gothic", "Century Gothic", sans-serif; }

  .spread {
    position: absolute; left: 0; top: 277px;
    width: 914px; height: 646px;
    display: flex;
    box-shadow: 0 10px 30px rgba(0,0,0,.18);
  }
  .panel { position: relative; width: 457px; height: 646px; overflow: hidden; background: var(--paper); }
  .panel svg.shapes { position: absolute; inset: 0; }

  /* Wordmark */
  .wordmark {
    display: flex; align-items: center; gap: 8px;
    color: var(--navy); font-family: "Didact Gothic", sans-serif;
    font-size: 22px; letter-spacing: .5px; text-transform: uppercase;
  }
  .wordmark .dot { width: 12px; height: 12px; border-radius: 50%; background: var(--red); }

  /* Back cover */
  .back { background: linear-gradient(135deg, var(--paper) 0%, var(--paper-shade) 100%); }
  .back .quote {
    position: absolute; left: 40px; right: 40px; top: 60px;
    font-family: "Libre Baskerville", serif; font-style: italic; font-weight: 700;
    font-size: 11.5px; line-height: 1.5; color: var(--navy); text-align: center;
  }
  .back .quote em { color: var(--red); font-style: italic; }
  .back .wordmark { position: absolute; left: 0; right: 0; top: 300px; justify-content: center; font-size: 20px; }
  .contact { position: absolute; left: 36px; bottom: 42px; width: 300px; color: var(--ink-soft); font-size: 8.5px; }
  .contact .lead { margin-bottom: 4px; }
  .contact h3 {
    font-family: "Didact Gothic", sans-serif; font-weight: 400; font-size: 15px;
    color: var(--navy); letter-spacing: .5px;
    border-bottom: 1px solid var(--red); padding-bottom: 4px; margin-bottom: 8px;
  }
  .contact .rows { display: grid; grid-template-columns: 1fr 1fr; gap: 5px 14px; }
  .contact .row { display: flex; align-items: center; gap: 5px; }
  .contact svg { width: 8px; height: 8px; fill: var(--red); flex: none; }

  /* Front cover */
  .front .wordmark { position: absolute; left: 0; right: 0; top: 48px; justify-content: center; }
  .photo {
    position: absolute; left: 0; right: 0; top: 108px; height: 420px;
    background: linear-gradient(120deg, #f3ece2 0%, #d9c2a6 35%, #8a93a8 60%, #f4d2a8 85%, #ffffff 100%);
  }
  .cover-copy { position: absolute; left: 0; right: 0; top: 520px; text-align: center; color: #fff; }
  .cover-copy h1 {
    font-family: "Montserrat", "Century Gothic", sans-serif; font-weight: 600;
    font-size: 27px; line-height: 1.05; letter-spacing: .5px;
  }
  .cover-copy h2 {
    font-family: "Montserrat", "Century Gothic", sans-serif; font-weight: 600;
    font-size: 18px; letter-spacing: .6px; margin-top: 2px;
  }
  .cover-copy p { font-size: 9px; line-height: 1.35; width: 330px; margin: 8px auto 0; opacity: .9; }
  .cover-copy .web {
    display: flex; align-items: center; justify-content: center; gap: 12px;
    margin-top: 12px; font-size: 12px;
  }
  .cover-copy .web::before, .cover-copy .web::after {
    content: ""; width: 60px; height: 1px; background: rgba(255,255,255,.6);
  }
</style>
</head>
<body>
  <main class="spread">
    <section class="panel back" aria-label="Back cover">
      <svg class="shapes" viewBox="0 0 457 646" aria-hidden="true">
        <path d="M330,646 Q400,560 457,535 L457,646 Z" fill="var(--red)"/>
      </svg>
      <p class="quote">If value, whether financial or relationship is not achieved, then we are not finished, <em>we have only just begun.</em></p>
      <div class="wordmark"><span class="dot"></span>Velt Advisory</div>
      <div class="contact">
        <p class="lead">For any commission enquiries, pricing, or any general enquiries please</p>
        <h3>CONTACT US</h3>
        <div class="rows">
          <div class="row"><svg viewBox="0 0 10 10"><path d="M5 0a3.5 3.5 0 0 1 3.5 3.5C8.5 6 5 10 5 10S1.5 6 1.5 3.5A3.5 3.5 0 0 1 5 0z"/></svg>48 Harbour Rd, Fairview, FL 32811</div>
          <div class="row"><svg viewBox="0 0 10 10"><path d="M2 0h2l1 3-1.5 1a6 6 0 0 0 2.5 2.5L7 5l3 1v2a2 2 0 0 1-2 2A8 8 0 0 1 0 2a2 2 0 0 1 2-2z"/></svg>(555) 014-2270</div>
          <div class="row"><svg viewBox="0 0 10 10"><circle cx="5" cy="5" r="4.5"/></svg>www.velt-advisory-partners.com</div>
          <div class="row"><svg viewBox="0 0 10 10"><path d="M0 2h10v6H0z"/></svg>info@velt-advisory-partners.com</div>
        </div>
      </div>
    </section>

    <section class="panel front" aria-label="Front cover">
      <div class="wordmark"><span class="dot"></span>Velt Advisory</div>
      <div class="photo" role="img" aria-label="Photograph of three consultants meeting at a bright office table"></div>
      <svg class="shapes" viewBox="0 0 457 646" aria-hidden="true">
        <path d="M0,512 Q220,412 457,418 L457,436 Q220,430 0,530 Z" fill="var(--navy)"/>
        <path d="M0,530 Q220,430 457,436 L457,646 L0,646 Z" fill="var(--red)"/>
      </svg>
      <div class="cover-copy">
        <h1>THE CONTRACT</h1>
        <h2>AND CONFLICT ADVISORY</h2>
        <p>We are an experienced contract and conflict advisory providing global contract performance solutions and conflict management</p>
        <div class="web">www.velt-advisory-partners.com</div>
      </div>
    </section>
  </main>
</body>
</html>
```